K7 Construction Site Sign

I would like to get a sign designed which would be installed at a construction sign. I would like to incorporate my current logo, font and colors in the sign. The sign would be 30" x 60" (vertical). Would like to keep it clean and simple yet eye catching and sparks interest. I have attached my branding colors. I would like the background to be the branded blue with white text.

```html
<!DOCTYPE html>
<html lang="en">
<head>
<meta charset="utf-8">
<title>K7 Construction Site Sign</title>
<link href="https://fonts.googleapis.com/css2?family=Montserrat:wght@400&display=swap" rel="stylesheet">
<style>
  :root {
    --brand-blue: #295381;
    --brand-gold: #d4a55a;
    --text-white: #ffffff;
    --page-bg: #ffffff;
  }
  * { margin: 0; padding: 0; box-sizing: border-box; }
  html, body {
    width: 1200px;
    height: 829px;
    overflow: hidden;
    background: var(--page-bg);
  }
  .canvas {
    position: relative;
    width: 1200px;
    height: 829px;
  }
  .site-sign {
    position: absolute;
    left: 420px;
    top: 54px;
    width: 360px;
    height: 720px;
    background: var(--brand-gold);
    box-shadow: 0 2px 6px rgba(0,0,0,0.25);
    overflow: hidden;
  }
  .sign-panel {
    position: absolute;
    left: 0;
    top: 0;
    width: 283px;
    height: 644px;
    background: var(--brand-blue);
    border-bottom-right-radius: 28px;
  }
  .brand-lockup {
    position: absolute;
    left: 78px;
    top: 593px;
    width: 560px;
    height: 126px;
    transform: rotate(-90deg);
    transform-origin: top left;
    display: flex;
    align-items: center;
    font-family: "Montserrat", sans-serif;
    font-weight: 400;
    color: var(--text-white);
  }
  .brand-mark {
    flex: none;
    width: 100px;
    display: flex;
    align-items: center;
    gap: 8px;
    font-size: 42px;
    line-height: 1;
  }
  .brand-square {
    width: 22px;
    height: 22px;
    background: var(--text-white);
    flex: none;
  }
  .company-title {
    margin-left: 12px;
    font-size: 40px;
    font-weight: 400;
    line-height: 58px;
    white-space: nowrap;
  }
  .company-title span { display: block; }
</style>
</head>
<body>
  <main class="canvas">
    <section class="site-sign" aria-label="K7 Crest Building and Renovation site sign">
      <div class="sign-panel">
        <div class="brand-lockup">
          <div class="brand-mark">
            <span class="brand-square"></span>
            <span class="brand-name">K7</span>
          </div>
          <h1 class="company-title">
            <span>CREST BUILDING &amp;</span>
            <span>RENOVATION LTD.</span>
          </h1>
        </div>
      </div>
    </section>
  </main>
</body>
</html>
```